Flyer Design Project with menu

We are from Juniper Table Restaurant. We usually serve breakfast, soul food, fried and BBQ Ribs , legs, wings etc. We located at 2870 n. Harlow street, canton, 39046, MS. Since this is a new restaurant we want to let people know about us. Please create a good professional flyer including menu on that. Thank you. Please let us know if you need any other information.
Updates

Target Market(s)

We want to attract customers from 3 different locations near 15 miles radius.

Industry/Entity Type

American Restaurant

Font styles to use
Serif

Requirements
Must have
• Good graphics with food pictures.
• Soul food graphic pictures, RIBS, FISH and breakfast regular.
Nice to have
• 20% discount coupon offer.

```html
<!DOCTYPE html>
<html lang="en">
<head>
<meta charset="utf-8">
<title>Juniper Table Restaurant – Menu Flyer</title>
<link href="https://fonts.googleapis.com/css2?family=Roboto+Slab:wght@500;700;800;900&display=swap" rel="stylesheet">
<style>
  :root {
    --red: #e2242a;
    --red-dark: #c61f26;
    --yellow: #fbe95a;
    --blue: #1f4fa3;
    --label-red: #e3262b;
    --grey-text: #4a4a4a;
    --panel: #eceded;
    --panel-line: #9a9a9a;
    --bg-light: #f2f2f2;
  }
  * { margin: 0; padding: 0; box-sizing: border-box; }
  html, body { width: 982px; height: 1200px; overflow: hidden; background: #fff; }
  .flyer { position: relative; width: 982px; height: 1200px; overflow: hidden;
    font-family: "Roboto Slab", Georgia, serif; color: var(--blue); background: var(--bg-light); }

  .header { position: absolute; left: 0; top: 0; width: 982px; height: 177px;
    background: linear-gradient(90deg, var(--red-dark) 0%, var(--red) 45%, var(--red-dark) 100%);
    border-bottom: 6px solid #c9c9c9;
    display: flex; align-items: center; justify-content: center; }
  .brand { font-family: "Roboto Slab", Georgia, serif; font-weight: 900;
    font-size: 46px; letter-spacing: 1px; color: var(--yellow); line-height: 1; white-space: nowrap; }

  .backdrop { position: absolute; left: 0; top: 183px; width: 982px; height: 1017px;
    background: radial-gradient(ellipse at 40% 55%, #cfcfcf 0%, #e4e4e4 45%, var(--bg-light) 80%); }
  .swoosh { position: absolute; left: 0; top: 900px; }

  .block { position: absolute; }
  .heading { font-weight: 900; font-size: 21px; line-height: 1; color: var(--blue); white-space: nowrap; }
  .subhead { font-weight: 700; font-style: italic; font-size: 19px; color: var(--label-red); white-space: nowrap; }
  .label { font-weight: 800; font-size: 14px; color: var(--label-red); }
  .item { position: absolute; font-weight: 800; font-size: 14.5px; white-space: nowrap; line-height: 1.2; }
  .note { position: absolute; font-weight: 700; font-style: italic; font-size: 18px; color: var(--label-red); line-height: 24px; }
  .served { position: absolute; font-weight: 700; font-size: 13.5px; color: var(--grey-text); line-height: 1.2; }

  .panel { position: absolute; background: var(--panel); border: 2px solid var(--panel-line); }
  .panel.center-text .item, .panel.center-text .label, .panel.center-text .served { left: 0; right: 0; text-align: center; }

  .fish-shape { position: absolute; left: 72px; top: 1029px; }
  .promo-title { position: absolute; left: 72px; width: 270px; top: 1072px; text-align: center;
    font-weight: 900; font-size: 21px; color: var(--blue); }
  .promo-sub { position: absolute; left: 72px; width: 270px; top: 1102px; text-align: center;
    font-weight: 700; font-style: italic; font-size: 19px; color: var(--label-red); }

  .drink-photo { position: absolute; left: 727px; top: 943px; width: 255px; height: 257px;
    background: linear-gradient(160deg, #f3efc0 0%, #eadc5a 45%, #f2c533 75%, #e9e9e9 100%);
    border-radius: 18px 18px 0 0; }
</style>
</head>
<body>
<main class="flyer">
  <div class="backdrop" role="img" aria-label="Faded photograph of a plate of soul food"></div>
  <svg class="swoosh" width="982" height="300" viewBox="0 0 982 300" aria-hidden="true">
    <path d="M0 40 Q 491 -10 982 30 L982 300 L0 300 Z" fill="#f7f7f7"/>
  </svg>

  <header class="header">
    <h1 class="brand">JUNIPER TABLE RESTAURANT</h1>
  </header>

  <section class="block breakfast" style="left:77px; top:222px;">
    <h2 class="heading">START YOUR DAY WITH US!</h2>
    <p class="subhead" style="margin-top:6px;">Breakfast starting at 6am</p>
  </section>
  <div class="item" style="left:77px; top:292px;">EGGS - 1.99</div>
  <div class="item" style="left:77px; top:323px;">SAUSAGE PATTIES - 2 for 1.99</div>
  <div class="item" style="left:77px; top:354px;">SMOKED LINK SAUSAGE - 2 for 1.99</div>
  <div class="item" style="left:77px; top:385px;">HASHBROWNS - 1.99</div>
  <div class="item" style="left:77px; top:416px;">BISCUITS - 1.99</div>
  <div class="item" style="left:77px; top:447px;">BAKED HAM - 1.99</div>
  <div class="item" style="left:77px; top:478px;">BACON - 1.99</div>
  <div class="item" style="left:77px; top:509px;">PAN CAKE - 1.99</div>
  <div class="item" style="left:77px; top:540px;">SANDWICHES - 2.99</div>

  <div class="item label" style="left:80px; top:656px;">SALADS:</div>
  <div class="item" style="left:80px; top:687px;">CHEF SALAD&nbsp; - 7.00</div>
  <div class="item" style="left:80px; top:718px;">GRILLED CHICKEN SALAD - 7.50</div>
  <div class="item" style="left:80px; top:749px;">POPCORN CHICKEN SALAD - 7.50</div>
  <div class="item label" style="left:80px; top:786px;">BURGERS:</div>
  <div class="item" style="left:80px; top:817px;">CLASSIC BURGER - 5.00</div>
  <div class="item" style="left:80px; top:848px;">CLASSIC CHEESEBURGER - 6.00</div>
  <div class="item" style="left:80px; top:879px;">BACON AND CHEESEBURGER - 7.00</div>
  <div class="item label" style="left:80px; top:918px;">RIBS:</div>
  <div class="item" style="left:80px; top:949px;">FULL RACK - 16.99</div>
  <div class="item" style="left:80px; top:980px;">HALF RACK - 8.99</div>

  <section class="block buffet" style="left:454px; top:220px;">
    <h2 class="heading">BUFFET Soul Food!</h2>
    <p class="subhead" style="margin-top:6px;">Create a plate from the line for only 7.99</p>
  </section>
  <div class="item label" style="left:454px; top:292px;">MAIN:</div>
  <div class="item" style="left:454px; top:323px;">RED BEANS with Rice &amp; Sausage</div>
  <div class="item" style="left:454px; top:354px;">BEEF TIPS with Rice</div>
  <div class="item" style="left:454px; top:385px;">TURKEY NECKS</div>
  <div class="item" style="left:454px; top:416px;">FRIED \ BAKED CHICKEN</div>
  <div class="item" style="left:454px; top:447px;">SPAGHETTI</div>
  <div class="item" style="left:454px; top:478px;">STUFFED BELL PEPPER (Shrimp,<br>Crab and Sausage)</div>
  <div class="item" style="left:454px; top:524px;">CHICKEN ON A STICK</div>
  <div class="item" style="left:454px; top:555px;">BREAD &amp; DRINK OF THE DAY</div>
  <p class="note" style="left:454px; top:592px;">* Buffet starting from 11am<br>till midnight 12pm</p>

  <div class="item label" style="left:758px; top:289px;">SIDES:</div>
  <div class="item" style="left:758px; top:320px;">RICE</div>
  <div class="item" style="left:758px; top:351px;">MAC N CHEESE</div>
  <div class="item" style="left:758px; top:382px;">COLLARD GREENS</div>
  <div class="item" style="left:758px; top:413px;">STRING BEANS</div>
  <div class="item" style="left:758px; top:444px;">BBQ RED BEANS</div>
  <div class="item" style="left:758px; top:475px;">MASH POTATOES</div>
  <div class="item" style="left:758px; top:506px;">CORN BREAD</div>
  <div class="item" style="left:758px; top:537px;">GREEN BEANS</div>
  <div class="item" style="left:758px; top:568px;">CORN</div>
  <div class="item" style="left:758px; top:599px;">YAMS</div>
  <div class="item" style="left:758px; top:630px;">CORNBREAD Dressing</div>

  <section class="panel combos" style="left:429px; top:685px; width:280px; height:482px;">
    <div class="item label" style="left:40px; top:28px;">FRIED CHICKEN</div>
    <div class="served" style="left:40px; top:46px;">(Served with 2sides)</div>
    <div class="item" style="left:40px; top:74px;">2 PC WHITE - 6.99</div>
    <div class="item" style="left:40px; top:105px;">2PC DARK - 4.99</div>
    <div class="item label" style="left:40px; top:152px;">STRIPS</div>
    <div class="served" style="left:40px; top:170px;">(Served with 2sides)</div>
    <div class="item" style="left:40px; top:199px;">3PC-3.95 MEAL - 5.99</div>
    <div class="item" style="left:40px; top:230px;">6PC-7.00 MEAL - 8.99</div>
    <div class="item" style="left:40px; top:261px;">9PC-10.99 MEAL - 12.99</div>
    <div class="item label" style="left:40px; top:314px;">SEA FOOD</div>
    <div class="served" style="left:40px; top:332px;">(Served with 2sides)</div>
    <div class="item" style="left:40px; top:360px;">2PC FRIED FISH - 8.99</div>
    <div class="item" style="left:40px; top:391px;">6PC SHRIMP - 6.99</div>
    <div class="item" style="left:40px; top:422px;">12PC SHRIMP - 11.99</div>
  </section>

  <section class="panel center-text extra-sides" style="left:707px; top:685px; width:222px; height:238px;">
    <div class="item label" style="top:32px;">SIDES</div>
    <div class="served" style="top:50px;">Individual - 2.00 /<br>Large - 4.00</div>
    <div class="item" style="top:95px;">OKRA</div>
    <div class="item" style="top:126px;">FRIES</div>
    <div class="item" style="top:157px;">BROCCOLI</div>
    <div class="item" style="top:188px;">SIDE SALAD</div>
  </section>

  <svg class="fish-shape" width="256" height="144" viewBox="0 0 256 144" role="img" aria-label="Outline of a fish">
    <ellipse cx="120" cy="72" rx="112" ry="52" fill="#f4f4f4" stroke="#cfcfcf" stroke-width="1.5"/>
  </svg>
  <p class="promo-title">SEA FOOD BUFFET</p>
  <p class="promo-sub">Coming Soon!</p>

  <div class="drink-photo" role="img" aria-label="Photograph of two glasses of lemonade with lemon slices"></div>
</main>
</body>
</html>
```